New signage for apartment community in the Pacific Northwest

Signage for an apartment community in the Pacific Northwest. It should have a contemporary northwest vibe with a fresh exciting feeling. We are open to the colors cayenne, white, charcoal and a splash of lime green. Sign to have the name 'VOLTE' with the address number 28351 smaller underneath. sign can include a shape under the name or a feeling of energy in the shape of the name.

Target Market(s)

Young urban professionals

Industry/Entity Type

Real Estate Development

Requirements
Must have
• eyecatching
Should not have
• anything too cute or too busy

```html
<!DOCTYPE html>
<html lang="en">
<head>
<meta charset="utf-8">
<title>VOLTE Signage</title>
<link rel="stylesheet" href="https://fonts.googleapis.com/css2?family=Abril+Fatface&family=Libre+Caslon+Text&display=swap">
<style>
  :root {
    --lime: #5bbb46;
    --charcoal: #25313b;
    --white: #ffffff;
    --backdrop: #eceeea;
    --letter-shadow: rgba(0, 0, 0, 0.55);
  }
  html, body {
    margin: 0;
    padding: 0;
    width: 1200px;
    height: 2503px;
    overflow: hidden;
    background: var(--backdrop);
  }
  .canvas {
    position: relative;
    width: 1200px;
    height: 2503px;
  }
  .sign {
    position: absolute;
    left: 60px;
    top: 531px;
    width: 1080px;
    height: 1440px;
  }
  .sign-frame {
    position: absolute;
    inset: 0;
    width: 1080px;
    height: 1440px;
  }
  .sign-frame .border { fill: var(--lime); }
  .sign-frame .panel { fill: var(--charcoal); }
  .sign-frame .corner { fill: var(--lime); }
  .sign-frame .keyline {
    fill: none;
    stroke: var(--white);
    stroke-width: 2.5;
  }
  .sign-name {
    position: absolute;
    left: 0;
    right: 0;
    top: 500px;
    margin: 0;
    text-align: center;
    font-family: "Abril Fatface", "Libre Caslon Text", serif;
    font-weight: 400;
    font-size: 268px;
    line-height: 1;
    letter-spacing: 10px;
    color: var(--lime);
    text-shadow: 4px 4px 3px var(--letter-shadow);
  }
  .sign-number {
    position: absolute;
    left: 0;
    right: 0;
    top: 800px;
    margin: 0;
    text-align: center;
    font-family: "Libre Caslon Text", serif;
    font-weight: 400;
    font-size: 108px;
    line-height: 1;
    letter-spacing: 2px;
    color: var(--lime);
    text-shadow: 2px 2px 2px var(--letter-shadow);
  }
</style>
</head>
<body>
<main class="canvas">
  <section class="sign">
    <svg class="sign-frame" viewBox="0 0 1080 1440" xmlns="http://www.w3.org/2000/svg" aria-hidden="true">
      <rect class="border" x="0" y="0" width="1080" height="1440"/>
      <rect class="panel" x="37" y="37" width="1006" height="1366"/>
      <circle class="corner" cx="37" cy="37" r="52"/>
      <circle class="corner" cx="1043" cy="37" r="52"/>
      <circle class="corner" cx="37" cy="1403" r="52"/>
      <circle class="corner" cx="1043" cy="1403" r="52"/>
      <path class="keyline" d="M104 70 H976 A75 75 0 0 0 1010 104 V1336 A75 75 0 0 0 976 1370 H104 A75 75 0 0 0 70 1336 V104 A75 75 0 0 0 104 70 Z"/>
    </svg>
    <h1 class="sign-name">VOLTE</h1>
    <p class="sign-number">28351</p>
  </section>
</main>
</body>
</html>
```